Meadowlark Property Review is a leading provider of residential appraisal and home inspection products in S

I need a business card/logo designed that obviously describes my business. We are a residential appraisal and home inspection company in Springfield, MO. We offer residential appraisals, home inspection, pest inspection and radon gas measurement. We have been in business for 18 years and hold state certified residential appraisal licenses and OBREX certified home inspection licenses. I have a logo that I really like and will attach, but would be open to new suggestions. I like more modern designs than traditional and would like a two sided card with our services, licenses and qualifications on the back.

```html
<!DOCTYPE html>
<html lang="en">
<head>
<meta charset="utf-8">
<title>Meadowlark Property Review – Business Card</title>
<link href="https://fonts.googleapis.com/css2?family=Open+Sans:ital,wght@0,400;0,600;1,400&display=swap" rel="stylesheet">
<style>
  :root{
    --stage:#2c2c2c;
    --paper:#ffffff;
    --bronze:#a3845c;
    --bronze-dark:#8c6d45;
    --bronze-light:#b89c76;
    --orange:#f5a01c;
    --orange-deep:#f39414;
    --orange-light:#f9b13a;
    --ink-light:#fbf6ee;
  }
  *{margin:0;padding:0;box-sizing:border-box}
  html,body{width:1200px;height:659px;overflow:hidden}
  body{
    background:var(--stage);
    font-family:"Open Sans",Arial,sans-serif;
    position:relative;
  }
  .card{
    position:absolute;
    top:187px;
    width:500px;height:286px;
    overflow:hidden;
    box-shadow:0 10px 24px rgba(0,0,0,.45);
  }
  /* front */
  .card--front{left:60px;background:var(--paper)}
  .front__band{position:absolute;inset:0}
  .brand{
    position:absolute;left:34px;top:92px;
    display:flex;align-items:center;gap:12px;
  }
  .brand__mark{width:16px;height:16px;background:var(--orange);flex:none}
  .brand__name{
    font-size:23px;font-weight:600;line-height:1.15;
    color:var(--bronze-dark);width:170px;
  }
  .contact{
    position:absolute;left:262px;top:0;width:238px;height:286px;
    color:var(--ink-light);
  }
  .person{position:absolute;left:22px;top:150px;font-size:12px;line-height:1.55}
  .person__name{color:var(--orange);font-size:16px;font-weight:600;margin-bottom:2px}
  .divider{position:absolute;left:20px;right:20px;top:136px;height:1px;background:rgba(255,255,255,.45)}
  .lines{position:absolute;left:22px;top:58px;list-style:none;font-size:12px;line-height:1.75}
  .lines li{display:flex;align-items:center;gap:8px}
  .lines svg{width:11px;height:11px;flex:none;fill:var(--orange)}
  /* back */
  .card--back{
    left:640px;
    background:linear-gradient(135deg,var(--orange-deep),var(--orange-light) 60%,var(--orange));
  }
  .services{
    position:absolute;left:34px;bottom:34px;
    list-style:none;color:#fff;font-style:italic;font-size:13px;line-height:1.6;
  }
  .services li::before{content:"• "}
</style>
</head>
<body>

<section class="card card--front" aria-label="Business card front">
  <svg class="front__band" viewBox="0 0 500 286" aria-hidden="true">
    <defs>
      <linearGradient id="bronzeFill" x1="0" y1="0" x2="1" y2="1">
        <stop offset="0" stop-color="#9a7a50"/>
        <stop offset="1" stop-color="#b89c76"/>
      </linearGradient>
    </defs>
    <polygon points="262,0 500,0 500,286 262,286 262,42 254,30 262,18" fill="url(#bronzeFill)"/>
    <polyline points="268,0 268,20 260,30 268,40 268,286" fill="none" stroke="#f1e6d6" stroke-width="1.2" opacity=".7"/>
  </svg>

  <div class="brand">
    <span class="brand__mark"></span>
    <span class="brand__name">Meadowlark Property Review</span>
  </div>

  <div class="contact">
    <ul class="lines">
      <li><svg viewBox="0 0 12 12"><path d="M2 1l2.5 0 1 3-1.5 1a7 7 0 0 0 3 3l1-1.5 3 1V10a1 1 0 0 1-1 1A9 9 0 0 1 1 2a1 1 0 0 1 1-1z"/></svg>417 555 0182</li>
      <li><svg viewBox="0 0 12 12"><rect x="1" y="4" width="10" height="6" rx="1"/><rect x="3" y="1" width="6" height="3"/></svg>417 555 0247</li>
      <li><svg viewBox="0 0 12 12"><path d="M1 2h10v8H1z M1 2l5 4 5-4" stroke="#8c6d45" stroke-width=".8"/></svg>dana@meadowlarkreview.com</li>
      <li><svg viewBox="0 0 12 12"><circle cx="6" cy="6" r="5"/></svg>www.meadowlarkreview.com</li>
    </ul>
    <div class="divider"></div>
    <div class="person">
      <p class="person__name">Dana Whitcombe</p>
      <p>CEO/Founder</p>
      <p>2210 Sycamore Court</p>
      <p>Springfield, Missouri 65804</p>
    </div>
  </div>
</section>

<section class="card card--back" aria-label="Business card back">
  <ul class="services">
    <li>Residential appraisals</li>
    <li>Home inspection</li>
    <li>Pest inspection</li>
    <li>Radon gas measurement.</li>
  </ul>
</section>

</body>
</html>
```